BorrowNest Website design, we are a home loan / lending company

We are a finance broking company that can do mortgages / home loans, Car Loans, Commercial Loans, SMSF Loans, Business Loans, Personal Loans
We are looking for a simple website, not too busy, easy to navigate, something that prompts customers to action or call us.
I like the simplicity of the following websites:
https://www.velkarafinance.com.au/ - I like this website front page. I was thinking I have my logo, the one with the black background appear , then the toolbar at the top perhaps?
https://trevix.com.au/business-loans# - on this page there are images under finance that works for you that I like that concept.
https://dunmerel.com.au/contact/ - I like the Make an Appointment page
https://trevix.com.au/about-us - Simple but effective page design

Target Market(s)

Home Loan Customer

Industry/Entity Type

Finance / Home Loans

Coding

Coded - Design and coding required

Number of Pages Required

5+ page

Font styles to use
Serif

Colors
0094D4
00A9DD
6FCCEA
C7EBF8
E9F6FB

Requirements
Must have
• The following Heading s - Contact Us, About Us, Our People, Make an Appointment, Loan Options, Calculators, Reviews. I want to use the Logo colours I have in the zip files I uploaded.
Nice to have
• Simple clean design

```html
<!DOCTYPE html>
<html lang="en">
<head>
<meta charset="utf-8">
<title>BorrowNest – Home Loans &amp; Lending</title>
<link href="https://fonts.googleapis.com/css2?family=Montserrat:wght@600;700;800&family=Roboto:ital,wght@0,400;0,500;0,700;1,400&display=swap" rel="stylesheet">
<style>
:root{
  --blue:#1689df;
  --blue-deep:#0f7fd6;
  --cyan:#1fe0f6;
  --ice:#def8fb;
  --ink:#222222;
  --text:#555555;
  --black:#000000;
  --white:#ffffff;
  --line:#8a8a8a;
  --star:#f0a31c;
}
*{box-sizing:border-box;margin:0;padding:0}
html,body{width:1200px;height:4409px;overflow:hidden;background:var(--white)}
body{font-family:"Roboto",Arial,sans-serif;color:var(--ink);position:relative}
.page{position:relative;width:1200px;height:4409px;overflow:hidden}
.abs{position:absolute}
.heading{font-family:"Montserrat",Arial,sans-serif;font-weight:800;color:var(--ink);letter-spacing:-.5px}
.btn{position:absolute;display:flex;align-items:center;justify-content:center;border-radius:30px;font-family:"Roboto",sans-serif;font-weight:700;font-size:16px;text-transform:uppercase;background:var(--blue);color:var(--white)}
.rule{position:absolute;height:3px;width:34px;background:var(--blue)}
.dots{position:absolute;background-image:radial-gradient(circle,#1c1c1c 1.6px,transparent 2.2px);background-size:19.5px 19.5px}

/* top bar */
.topbar{position:absolute;left:0;top:0;width:1200px;height:68px;background:var(--black)}
.brand{font-family:"Montserrat",sans-serif;font-weight:600;color:var(--white);letter-spacing:-1px}
.topbar .brand{position:absolute;left:142px;top:10px;font-size:38px}
.contact{position:absolute;right:168px;top:22px;color:var(--white);font-weight:700;font-size:17px;display:flex;align-items:center;gap:6px}
.contact .sep{margin:0 8px}
.mainnav{position:absolute;left:0;top:68px;width:1200px;height:42px;background:linear-gradient(90deg,var(--cyan),var(--blue) 70%,var(--blue-deep))}
.mainnav ul{list-style:none;position:absolute;left:144px;top:0;height:42px;display:flex}
.mainnav li{font-size:12px;font-weight:500;color:var(--white);line-height:42px;padding:0 12.5px}
.mainnav li.active{background:#2b2b2b}
.search{position:absolute;left:1037px;top:80px}

/* hero */
.hero{position:absolute;left:0;top:110px;width:1200px;height:588px;background:linear-gradient(120deg,#2e2f33 0%,#5b5048 40%,#8c7866 62%,#c8c2bb 100%)}
.hero .brand{position:absolute;left:0;width:1200px;top:170px;text-align:center;font-size:104px;letter-spacing:-3px}
.hero-dot{position:absolute;left:1150px;width:9px;height:9px;border-radius:50%;background:var(--white)}

/* services */
.services{position:absolute;left:146px;top:608px;width:907px;height:560px;display:grid;grid-template-columns:repeat(3,1fr);grid-template-rows:repeat(2,1fr);background:var(--white);box-shadow:0 4px 18px rgba(0,0,0,.12)}
.service{position:relative;text-align:center;border:1px solid #eeeeee;padding-top:24px}
.service svg{display:block;margin:0 auto;width:70px;height:70px}
.service h3{font-size:15px;font-weight:500;margin-top:21px;color:var(--ink)}
.service p{font-size:11px;line-height:21.5px;color:var(--text);margin:11px auto 0;width:236px}
.service .more{display:block;margin-top:13px;font-size:13px;font-weight:700;color:var(--blue)}
.service.featured{background:linear-gradient(110deg,var(--cyan),var(--blue) 95%)}
.service.featured h3,.service.featured p,.service.featured .more{color:var(--white)}

/* about */
.about-title{position:absolute;left:156px;top:1268px;font-size:68px}
.about-copy{position:absolute;left:156px;top:1370px;width:443px;font-size:13.2px;line-height:25.7px;color:var(--text);text-align:justify}
.about-frame{position:absolute;left:680px;top:1229px;width:365px;height:432px;background:var(--blue);border-radius:182px 182px 182px 150px}
.about-photo{position:absolute;left:680px;top:1275px;width:347px;height:345px;background:linear-gradient(135deg,#e5dcd2,#9c8b7c 55%,#5b4f47);border-radius:170px 170px 130px 0}

/* loan options */
.loan-photo{position:absolute;left:144px;top:1847px;width:383px;height:565px;background:linear-gradient(160deg,#c7b79e,#6e6158 50%,#3d3a3a)}
.loan-frame{position:absolute;left:72px;top:2154px;width:241px;height:356px;border:4px solid var(--blue)}
.loan-title{position:absolute;left:609px;top:1910px;font-size:64px}
.checks{position:absolute;left:609px;top:2032px;list-style:none}
.checks li{display:flex;align-items:center;height:33.6px;font-size:16px;color:var(--ink)}
.checks svg{width:18px;height:14px;margin:0 21px 0 7px}

/* appointment */
.appt-title{position:absolute;left:0;width:1200px;text-align:center;top:2645px;font-size:68px}
.label{position:absolute;font-size:16px;color:var(--ink)}
.field{position:absolute;border:1px solid #6f6f6f;background:var(--white)}
.terms{position:absolute;left:204px;top:3405px;font-size:14px;font-style:italic;color:#333;display:flex;align-items:center;gap:11px}
.terms .box{width:12px;height:12px;border:1px solid #444}

/* reviews */
.footer-band{position:absolute;left:0;top:3958px;width:1200px;height:451px;background:var(--black)}
.reviews-title{position:absolute;left:0;width:1200px;text-align:center;top:3615px;font-size:66px}
.review{position:absolute;top:3778px;width:330px}
.avatar{position:absolute;left:0;top:0;width:68px;height:68px;border-radius:50%;border:2px solid #d5d5d5;background:linear-gradient(160deg,#d9cbbf,#8a7f78)}
.review .quote{position:absolute;left:88px;top:8px;width:235px;font-size:11px;font-style:italic;line-height:23px;color:#6a6a6a}
.review .quote b{color:var(--blue);font-size:16px;font-weight:700;margin-right:6px}
.review .name{position:absolute;left:88px;top:94px;font-size:9.5px;color:var(--ink);text-transform:uppercase}
.review .role{position:absolute;left:88px;top:108px;font-size:9px;font-style:italic;color:var(--ink);white-space:nowrap}
.review .stars{position:absolute;left:84px;top:142px;font-size:18px;color:var(--star);letter-spacing:2px}

/* footer */
.footer .brand{position:absolute;left:224px;top:4208px;font-size:56px;letter-spacing:-2px}
.social{position:absolute;top:4297px;width:34px;height:34px;border-radius:50%;background:var(--blue);border:2px solid var(--white)}
.copyright{position:absolute;left:219px;top:4359px;font-size:12px;color:var(--white)}
.news-title{position:absolute;left:678px;top:4227px;font-size:20px;font-weight:700;color:var(--white)}
.news-input{position:absolute;left:678px;top:4273px;width:301px;height:37px;border-radius:20px;background:var(--white);font-size:13px;color:#888;padding:11px 20px}
</style>
</head>
<body>
<div class="page">

  <!-- header -->
  <header class="topbar">
    <div class="brand">BorrowNest</div>
    <div class="contact">
      <svg width="22" height="22" viewBox="0 0 24 24"><circle cx="12" cy="12" r="11" fill="none" stroke="#1689df" stroke-width="2"/><path d="M8 6.5c.6-.5 1.4-.4 1.8.2l1 1.6c.3.5.2 1.1-.2 1.5l-.7.6c.6 1.3 1.6 2.4 2.9 3l.6-.7c.4-.4 1-.5 1.5-.2l1.6 1c.6.4.7 1.2.2 1.8l-.7.8c-.6.6-1.5.8-2.3.5-3.2-1.2-5.6-3.7-6.8-6.8-.3-.8-.1-1.7.5-2.3z" fill="#1689df"/></svg>
      <span>+1 800 555 0142</span><span class="sep">|</span><span>LOGIN</span>
    </div>
  </header>
  <nav class="mainnav">
    <ul>
      <li class="active">HOME</li><li>CONTACT US</li><li>ABOUT US</li><li>OUR PEOPLE</li><li>MAKE AN APPOINTMENT</li><li>LOAN OPTIONS</li><li>CALCULATORS</li><li>REVIEWS</li>
    </ul>
  </nav>
  <svg class="search" width="18" height="18" viewBox="0 0 20 20"><circle cx="8" cy="8" r="6" fill="none" stroke="#fff" stroke-width="2.5"/><path d="M12.5 12.5l5 5" stroke="#fff" stroke-width="3" stroke-linecap="round"/></svg>

  <!-- hero -->
  <section class="hero" role="img" aria-label="Photo of a professional woman signing loan papers at a desk beside a small model house">
    <div class="brand">BorrowNest</div>
    <span class="hero-dot" style="top:357px"></span>
    <span class="hero-dot" style="top:381px;background:var(--blue)"></span>
    <span class="hero-dot" style="top:407px"></span>
  </section>
  <div class="btn" style="left:382px;top:438px;width:171px;height:55px">Get Started</div>
  <div class="btn" style="left:565px;top:438px;width:252px;height:55px;background:var(--white);color:var(--blue)">Make an Appointment</div>

  <!-- services -->
  <div class="dots" style="left:66px;top:1096px;width:136px;height:136px"></div>
  <section class="services">
    <article class="service">
      <svg viewBox="0 0 70 70" fill="none" stroke="#1689df" stroke-width="2"><path d="M8 32L30 12l22 20"/><path d="M14 27v28h26"/><rect x="22" y="38" width="10" height="17"/><rect x="34" y="18" width="5" height="8"/><circle cx="50" cy="50" r="12" fill="#e6f7fd"/><path d="M53 45h-5a2.5 2.5 0 000 5h4a2.5 2.5 0 010 5h-5M50 42v16"/></svg>
      <h3>MORTGAGES/HOME LOANS</h3>
      <p>Lorem ipsum dolor sit amet, consectetur adipiscing elit, sed do eiusmod tempor incididunt ut labore et dolore magna aliqua. Quis ipsum suspendisse ultrices</p>
      <span class="more">READ MORE</span>
    </article>
    <article class="service">
      <svg viewBox="0 0 70 70" fill="none" stroke="#1689df" stroke-width="2"><rect x="22" y="6" width="26" height="13" fill="#e6f7fd"/><path d="M30 19v6h10v-6"/><path d="M12 46l5-14c1-3 3-5 6-5h24c3 0 5 2 6 5l5 14v12H12z"/><circle cx="22" cy="50" r="4"/><circle cx="48" cy="50" r="4"/><path d="M17 40h36"/></svg>
      <h3>CAR LOANS</h3>
      <p>Lorem ipsum dolor sit amet, consectetur adipiscing elit, sed do eiusmod tempor incididunt ut labore et dolore magna aliqua. Quis ipsum suspendisse ultrices</p>
      <span class="more">READ MORE</span>
    </article>
    <article class="service">
      <svg viewBox="0 0 70 70" fill="none" stroke="#1689df" stroke-width="2"><rect x="10" y="30" width="16" height="32"/><rect x="28" y="8" width="18" height="54" fill="#e6f7fd"/><rect x="46" y="22" width="14" height="40"/><path d="M32 16h10M32 24h10M32 32h10M32 40h10M32 48h10M14 38h8M14 46h8M50 30h6M50 38h6M50 46h6M6 62h58"/></svg>
      <h3>COMMERCIAL LOANS</h3>
      <p>Lorem ipsum dolor sit amet, consectetur adipiscing elit, sed do eiusmod tempor incididunt ut labore et dolore magna aliqua. Quis ipsum suspendisse ultrices</p>
      <span class="more">READ MORE</span>
    </article>
    <article class="service">
      <svg viewBox="0 0 70 70" fill="none" stroke="#1689df" stroke-width="2"><circle cx="38" cy="28" r="16" fill="#e6f7fd"/><path d="M42 21h-6a3 3 0 000 6h4a3 3 0 010 6h-6M38 17v20"/><path d="M8 52l10-6c3-2 6-2 9 0l7 3h10c2 0 2 4 0 4H30M8 62l10-4 16 3 20-10"/></svg>
      <h3>SMSF LOANS</h3>
      <p>Lorem ipsum dolor sit amet, consectetur adipiscing elit, sed do eiusmod tempor incididunt ut labore et dolore magna aliqua. Quis ipsum suspendisse ultrices</p>
      <span class="more">READ MORE</span>
    </article>
    <article class="service featured">
      <svg viewBox="0 0 70 70" fill="none" stroke="#ffffff" stroke-width="2"><path d="M14 8h32l8 8v46H14z"/><rect x="20" y="12" width="20" height="10"/><path d="M20 30h26M20 37h26M20 44h18M20 51h14"/><path d="M50 48l12-24 4 2-12 24-5 3z"/></svg>
      <h3>BUSINESS LOANS</h3>
      <p>Lorem ipsum dolor sit amet, consectetur adipiscing elit, sed do eiusmod tempor incididunt ut labore et dolore magna aliqua. Quis ipsum suspendisse ultrices</p>
      <span class="more">READ MORE</span>
    </article>
    <article class="service">
      <svg viewBox="0 0 70 70" fill="none" stroke="#1689df" stroke-width="2"><path d="M14 8h32l8 8v46H14z" fill="#e6f7fd"/><circle cx="33" cy="24" r="6"/><path d="M23 40c1-6 5-8 10-8s9 2 10 8"/><path d="M20 48h26M20 55h18"/><path d="M50 50l12-22 4 2-12 22-5 3z"/></svg>
      <h3>PERSONAL LOANS</h3>
      <p>Lorem ipsum dolor sit amet, consectetur adipiscing elit, sed do eiusmod tempor incididunt ut labore et dolore magna aliqua. Quis ipsum suspendisse ultrices</p>
      <span class="more">READ MORE</span>
    </article>
  </section>

  <!-- about -->
  <h2 class="heading about-title">About Us</h2>
  <p class="about-copy">Lorem ipsum dolor sit amet, consectetur adipiscing elit, sed do eiusmod tempor incididunt ut labore et dolore magna aliqua. Quis ipsum suspendisse ultrices gravida. Risus commodo viverra maecenas accumsan lacus vel facilisis. Lorem ipsum dolor sit amet, consectetur adipiscing elit, sed do eiusmod tempor incididunt ut labore et dolore magna aliqua. Quis ipsum suspendisse ultrices gravida. Risus commodo viverra maecenas accumsan lacus vel facilisis.</p>
  <div class="btn" style="left:156px;top:1584px;width:173px;height:55px">Read More</div>
  <div class="about-frame"></div>
  <div class="about-photo" role="img" aria-label="Photo of two businesswomen reviewing documents at a table"></div>
  <div class="dots" style="left:986px;top:1604px;width:118px;height:118px;-webkit-mask:linear-gradient(90deg,transparent 0 40%,#000 40%) top/100% 40% no-repeat,linear-gradient(#000,#000) bottom/100% 60% no-repeat"></div>

  <!-- loan options -->
  <svg class="abs" style="left:0;top:0" width="1200" height="2600" viewBox="0 0 1200 2600" aria-hidden="true">
    <defs><linearGradient id="loanFill" x1="0" y1="0" x2="1" y2="1"><stop offset="0" stop-color="#d8f2f6"/><stop offset=".5" stop-color="#e8f5f7"/><stop offset="1" stop-color="#cfeef4"/></linearGradient></defs>
    <path d="M21 1775Q21 1758 40 1758L880 1758C1070 1758 1180 1900 1180 2090L1180 2300C1180 2440 1090 2534 960 2534L540 2534C240 2534 21 2260 21 1960Z" fill="url(#loanFill)" stroke="#7fb7bd" stroke-width="1"/>
  </svg>
  <div class="loan-photo" role="img" aria-label="Photo of a smiling businesswoman meeting a client over paperwork"></div>
  <div class="loan-frame"></div>
  <div class="dots" style="left:32px;top:2429px;width:120px;height:120px"></div>
  <h2 class="heading loan-title">Loan Options</h2>
  <div class="rule" style="left:609px;top:2001px"></div>
  <ul class="checks">
    <li><svg viewBox="0 0 18 14"><path d="M1 7l5 5L17 1" fill="none" stroke="#1689df" stroke-width="3"/></svg>Borrow $5,000 – $250,000</li>
    <li><svg viewBox="0 0 18 14"><path d="M1 7l5 5L17 1" fill="none" stroke="#1689df" stroke-width="3"/></svg>12 – 24 month loan terms</li>
    <li><svg viewBox="0 0 18 14"><path d="M1 7l5 5L17 1" fill="none" stroke="#1689df" stroke-width="3"/></svg>No asset security required</li>
    <li><svg viewBox="0 0 18 14"><path d="M1 7l5 5L17 1" fill="none" stroke="#1689df" stroke-width="3"/></svg>Apply online in 7 minutes</li>
    <li><svg viewBox="0 0 18 14"><path d="M1 7l5 5L17 1" fill="none" stroke="#1689df" stroke-width="3"/></svg>Credit decisions within 24 hours</li>
    <li><svg viewBox="0 0 18 14"><path d="M1 7l5 5L17 1" fill="none" stroke="#1689df" stroke-width="3"/></svg>No penalty for early repayment</li>
  </ul>
  <div class="btn" style="left:609px;top:2261px;width:173px;height:55px">Read More</div>

  <!-- appointment -->
  <h2 class="heading appt-title">Make an Appointment</h2>
  <div class="rule" style="left:583px;top:2754px"></div>
  <span class="label" style="left:204px;top:2820px">First Name</span>
  <span class="label" style="left:609px;top:2820px">Last Name</span>
  <div class="field" style="left:204px;top:2854px;width:387px;height:60px"></div>
  <div class="field" style="left:609px;top:2854px;width:387px;height:60px"></div>
  <span class="label" style="left:204px;top:2943px">Email address</span>
  <span class="label" style="left:609px;top:2943px">Phone number</span>
  <div class="field" style="left:204px;top:2977px;width:387px;height:60px"></div>
  <div class="field" style="left:609px;top:2977px;width:387px;height:60px"></div>
  <span class="label" style="left:204px;top:3066px">Where do you live?</span>
  <div class="field" style="left:204px;top:3100px;width:792px;height:60px">
    <svg class="abs" style="right:18px;top:26px" width="14" height="8" viewBox="0 0 14 8"><path d="M0 0h14L7 8z" fill="#222"/></svg>
  </div>
  <span class="label" style="left:204px;top:3190px">Where do you live?</span>
  <div class="field" style="left:204px;top:3224px;width:792px;height:149px"></div>
  <div class="terms"><span class="box"></span>By getting started you are agreeing to our Terms &amp; Conditions</div>
  <div class="btn" style="left:823px;top:3388px;width:172px;height:55px">Submit</div>

  <!-- reviews -->
  <div class="footer-band"></div>
  <div class="dots" style="left:24px;top:3567px;width:118px;height:118px"></div>
  <svg class="abs" style="left:0;top:3500px" width="1200" height="700" viewBox="0 3500 1200 700" aria-hidden="true">
    <path d="M210 3539L1180 3539L1180 3790C1180 4000 920 4157 470 4157C190 4157 21 4010 21 3850C21 3660 90 3539 210 3539Z" fill="#dcfafc" stroke="#7fb7bd" stroke-width="1"/>
  </svg>
  <div class="dots" style="left:1087px;top:3833px;width:98px;height:118px;-webkit-mask:linear-gradient(90deg,transparent 0 33%,#000 33%) top/100% 50% no-repeat,linear-gradient(#000,#000) bottom/100% 50% no-repeat"></div>
  <h2 class="heading reviews-title">Reviews</h2>
  <div class="rule" style="left:583px;top:3718px"></div>

  <article class="review" style="left:130px">
    <div class="avatar" role="img" aria-label="Portrait photo of the reviewer"></div>
    <p class="quote"><b>“</b>At vero eos et accusamus et iustodio dignissimos ducimus qui blanditiipraesnt ium voluptatum deleniti atq.</p>
    <div class="name">Marisol Tenney</div>
    <div class="role">Financial Services Professional</div>
    <div class="stars">★★★★☆</div>
  </article>
  <article class="review" style="left:457px">
    <div class="avatar" role="img" aria-label="Portrait photo of the reviewer"></div>
    <p class="quote"><b>“</b>At vero eos et accusamus et iustodio dignissimos ducimus qui blanditiipraesnt ium voluptatum deleniti atqu.</p>
    <div class="name">Odessa R. Quillan</div>
    <div class="role">National Urban Fellow at the Brayfield</div>
    <div class="stars">★★★★<span style="background:linear-gradient(90deg,var(--star) 50%,#f6d79a 50%);-webkit-background-clip:text;color:transparent">★</span></div>
  </article>
  <article class="review" style="left:781px">
    <div class="avatar" role="img" aria-label="Portrait photo of the reviewer"></div>
    <p class="quote"><b>“</b>At vero eos et accusamus et iustodio dignissimos ducimus qui blanditiipraesnt ium voluptatum deleniti atqu.</p>
    <div class="name">Ivy Harrowgate</div>
    <div class="role">Creative Strategist | Entrepreneur &amp; Upcoming</div>
    <div class="stars">★★★★☆</div>
  </article>
  <div class="btn" style="left:491px;top:4006px;width:216px;height:55px">More Reviews</div>

  <!-- footer -->
  <footer class="footer">
    <div class="brand">BorrowNest</div>
    <span class="social" style="left:219px" aria-label="Social link"></span>
    <span class="social" style="left:264px" aria-label="Social link"></span>
    <span class="social" style="left:310px" aria-label="Social link"></span>
    <p class="copyright">Copyright © 2022 BorrowNest.All Rights Reserved &nbsp;|&nbsp; Privacy</p>
    <h4 class="news-title">SIGN UP TO NEWSLETTER</h4>
    <div class="news-input">Email Address</div>
    <div class="btn" style="left:678px;top:4324px;width:113px;height:43px;font-size:14px">Sign Up</div>
  </footer>

</div>
</body>
</html>
```